Brimcraft sales

🎨 Project Title:
Brimcraft Designer Web Page for WooCommerce (French Texts Provided) i show you exemple what i need

📄 Project Description:
We are looking to create a web page design (desktop and mobile) for a custom cap ordering experience. This page will be integrated into our existing WooCommerce transactional site. The goal is to allow customers to configure and order personalized caps easily and visually.

The entire interface will ultimately be in French, but you can design using placeholder texts (we will provide the actual French text later).

💡 Page Goals & Features:
The page should be modern, clean, and conversion-oriented, and include the following features:

Header area:

Visually showcase examples of designed caps (carousel or grid layout)

A clear title and short description

Customization Steps (in order):

Material selection: users choose the type of material for the cap

Cap color: users choose the base color of the cap

Patch shape: users select the shape of the patch (e.g., round, square, rectangle, custom)

Patch location: mainly the front, but possibly add other options

Quantity selection: users choose how many units they want (with price updates)

Price display: show price per unit and total cost depending on quantity

Call to Action (CTA):

Add to cart or request a quote button

Smooth integration with WooCommerce logic (cart, checkout, etc.)

Other Optional Sections:

FAQ

Delivery timeline

Client testimonials or reviews

🛠 Technical Notes:
The design must be compatible with WooCommerce

Responsive design for both desktop and mobile

The final output can be delivered in Figma, Adobe XD, or layered PSD (no coding required for now)

We will handle the French translation; just use placeholder text where needed

🖼 Inspiration / Style:
Clean and modern layout

Easy to navigate

Visual configurator-style approach (like t-shirt or shoe customization sites)

Feel free to use mockups of caps to enhance the presentation

📎 What we will provide:
Actual French text

Product images (caps, patch styles, color swatches)

Brand logo and colors

Optional references if needed

✅ Deliverables:
Homepage (or dedicated product page) layout

Mobile and desktop views

Editable design file (Figma, XD, PSD)

i need very nice 1 or 2 hat design to present to customer design un der the hat and front and see coupple of shape of the patche to show option possible

```html
<!DOCTYPE html>
<html lang="en">
<head>
<meta charset="utf-8">
<title>Brimcraft – Custom Hats</title>
<link rel="stylesheet" href="https://fonts.googleapis.com/css2?family=Audiowide&family=Montserrat:wght@400;500;600;700&display=swap">
<style>
:root{
  --bg:#121212;
  --panel:#1d1d1d;
  --bar:#1a1a1a;
  --nav:#0b0b0b;
  --red:#e0222f;
  --red-dark:#8d0f18;
  --white:#ffffff;
  --muted:#b9b9b9;
  --line:#cfcfcf;
  --star:#f5b400;
  --card:#f3f3f3;
  --footer:#1c1c1c;
}
*{box-sizing:border-box;margin:0;padding:0}
html,body{width:1200px;height:3530px;overflow:hidden}
body{background:var(--bg);color:var(--white);font-family:"Montserrat",sans-serif;position:relative;
  background-image:linear-gradient(135deg,transparent 40%,rgba(255,255,255,.025) 40%,rgba(255,255,255,.025) 55%,transparent 55%),
  linear-gradient(45deg,transparent 60%,rgba(255,255,255,.02) 60%,rgba(255,255,255,.02) 75%,transparent 75%)}
.abs{position:absolute}
.display{font-family:"Audiowide",sans-serif}

.topbar{left:0;top:0;width:1200px;height:43px;background:var(--bar);display:flex;align-items:center;justify-content:center;font-size:13px}
.topbar .close{position:absolute;right:22px;top:11px}
.nav{left:0;top:43px;width:1200px;height:86px;background:var(--nav)}
.brand{left:111px;top:24px;font-family:"Montserrat",sans-serif;font-weight:700;font-size:29px;letter-spacing:.5px}
.menu{left:427px;top:32px;display:flex;gap:27px;font-size:15px}
.menu .active{color:var(--red);font-weight:600}
.nav-icons{left:968px;top:28px;display:flex;gap:20px}
.badge{position:absolute;left:20px;top:-6px;width:14px;height:14px;border-radius:50%;background:var(--red);font-size:9px;display:flex;align-items:center;justify-content:center}

.hero{left:0;top:129px;width:1200px;height:490px;overflow:hidden;
  background:linear-gradient(120deg,#3a0a0e 0%,#150507 30%,#0d0d0d 55%,#1b0507 80%,#3b0a10 100%)}
.hero-streaks{left:0;top:0}
.hero-photo{left:616px;top:12px;width:584px;height:478px;
  background:radial-gradient(ellipse at 55% 30%,#c9a466 0%,#b78a4a 18%,transparent 34%),
  radial-gradient(ellipse at 58% 78%,#f2c21c 0%,#d9a50f 35%,transparent 62%),#1a0d0a;
  clip-path:polygon(18% 0,100% 0,100% 100%,0 100%,10% 70%)}
.hero h1{left:111px;top:88px;font-size:56px;line-height:68px;font-weight:400}
.hero h1 .hl{color:var(--red)}
.hero p{left:111px;top:257px;width:500px;font-size:17px;line-height:27px}

.btn{display:inline-flex;height:36px;border-radius:4px;overflow:hidden;font-size:15px;font-weight:500}
.btn .label{background:var(--red);display:flex;align-items:center;padding:0 34px 0 13px;color:var(--white)}
.btn .go{background:var(--white);width:56px;margin-left:-22px;clip-path:polygon(40% 0,100% 0,100% 100%,0 100%);display:flex;align-items:center;justify-content:flex-end;padding-right:14px}
.hero .btn{left:111px;top:353px}

.products{left:78px;top:707px;width:1044px;height:1219px;background:var(--panel);border-radius:26px}
.section-title{font-size:37px;text-align:center;width:100%}
.swoosh{display:block;margin:4px auto 0}
.products .section-title{position:absolute;top:52px}

.product-box{left:153px;top:860px;width:891px;height:587px;border:1px solid var(--line)}
.product-photo{left:30px;top:108px;width:324px;height:250px;border-radius:50% 50% 45% 45%/40% 40% 60% 60%;
  background:radial-gradient(ellipse at 50% 40%,#d9c49a 0%,#b89e70 55%,#7b2a3a 75%,transparent 78%)}
.dots{display:flex;gap:9px}
.dots span{width:11px;height:11px;border-radius:50%;background:var(--white)}
.dots span.on{background:var(--red)}
.product-box .dots{position:absolute;left:165px;top:396px}
.vdivider{left:401px;top:72px;width:1px;height:390px;background:#6d6d6d}
.info{left:449px;top:0}
.info h2{position:absolute;left:0;top:28px;font-size:36px;font-weight:500;white-space:nowrap}
.stars{display:flex;gap:1px}
.info .stars{position:absolute;left:2px;top:82px}
.info .price{position:absolute;left:1px;top:112px;font-size:25px;font-weight:400}
.info .desc{position:absolute;left:2px;top:154px;width:380px;font-size:12.5px;line-height:21px;color:var(--muted)}
.opt{position:absolute;left:0;font-size:17px;font-weight:500;white-space:nowrap}
.select{position:absolute;left:93px;top:218px;width:171px;height:30px;border:1px solid #9a9a9a;border-radius:4px;font-size:12px;color:#9a9a9a;display:flex;align-items:center;justify-content:space-between;padding:0 10px}
.swatch{position:absolute;top:270px;width:30px;height:30px;border-radius:50%}
.choices{position:absolute;display:flex;align-items:center;gap:12px;font-size:13px;color:var(--muted);white-space:nowrap}
.chip{background:var(--red);color:var(--white);padding:6px 13px;border-radius:3px}
.chip-outline{border:1px solid #9a9a9a;color:var(--white);padding:6px 15px;border-radius:3px}
.qty{position:absolute;left:3px;top:428px;display:flex;border:1px solid #9a9a9a;border-radius:3px;height:37px}
.qty span{width:38px;display:flex;align-items:center;justify-content:center;font-size:17px}
.qty span+span{border-left:1px solid #9a9a9a}
.info .actions{position:absolute;left:3px;top:490px;display:flex;gap:15px}
.info .note{position:absolute;left:0;top:539px;font-size:12px;color:var(--muted);white-space:nowrap}

.arrow-btn{width:57px;height:57px;border-radius:50%;background:var(--red);display:flex;align-items:center;justify-content:center}
.thumb{position:absolute;top:1502px;width:274px;height:265px;background:#0d0d0d}
.thumb .hat{position:absolute;left:40px;top:55px;width:194px;height:150px;border-radius:50% 50% 45% 45%/45% 45% 55% 55%;background:radial-gradient(ellipse at 50% 45%,#e3d2a6 0%,#cbb27c 60%,transparent 72%)}
.thumb-meta{position:absolute;top:1790px;width:274px}
.thumb-meta h3{font-size:19px;font-weight:500}
.thumb-meta .stars{margin-top:6px}
.thumb-meta .p{margin-top:14px;font-size:15px;color:var(--muted)}

.tabs{left:111px;top:2004px;display:flex;gap:60px;font-size:34px}
.tabs .on{color:var(--red)}
.tabs .off{color:#8c8c8c;font-size:29px;padding-top:4px}
.tabs-line{left:78px;top:2073px;width:1044px;height:1px;background:#8c8c8c}
.faq{position:absolute;left:111px;width:978px;height:49px;border:1px solid var(--line);border-radius:11px;display:flex;align-items:center;justify-content:space-between;padding:0 20px;font-size:14.5px}
.plus{width:29px;height:29px;border-radius:50%;background:var(--white);display:flex;align-items:center;justify-content:center}

.reviews-title{left:0;top:2645px;width:1200px}
.review{position:absolute;top:2767px;width:296px;height:291px;background:var(--card);border-radius:12px;color:#222;padding:28px 22px}
.review .q{font-family:Georgia,serif;font-size:44px;line-height:24px;font-weight:700;color:#222}
.review .stars{position:absolute;right:22px;top:34px}
.review p{margin-top:28px;font-size:12.5px;line-height:21px;color:#666}
.review .who{position:absolute;left:22px;top:218px;display:flex;align-items:center;gap:16px}
.avatar{width:46px;height:46px;border-radius:50%;background:var(--red);color:var(--white);display:flex;align-items:center;justify-content:center;font-size:17px;font-weight:700}
.who b{display:block;font-weight:500;font-size:14px;color:#222}
.who small{font-size:11.5px;color:#999}
.review-dots{left:565px;top:3094px;display:flex;gap:8px}
.review-dots span{width:11px;height:11px;border-radius:50%;background:#777}
.review-dots span.on{width:14px;height:14px;margin-top:-1px;background:var(--red)}

.footer{left:0;top:3196px;width:1200px;height:334px;background:var(--footer)}
.col{position:absolute;top:56px}
.col h4{font-family:"Audiowide",sans-serif;font-weight:400;font-size:22px;margin-bottom:22px;white-space:nowrap}
.col ul{list-style:none;font-size:15px;line-height:30px;color:#d9d9d9}
.col p{font-size:15px;line-height:22px;color:#d9d9d9;width:270px}
.email{margin-top:18px;width:358px;height:36px;border:1px solid #8c8c8c;border-radius:4px;display:flex;align-items:center;justify-content:space-between;padding:0 12px;font-size:13px;color:#8c8c8c}
.foot-line{left:0;top:3463px;width:1200px;height:1px;background:#3a3a3a}
.copy{left:111px;top:3489px;font-size:13.5px;color:#d9d9d9}
.cards{left:884px;top:3486px;display:flex;gap:9px}
.cards span{width:27px;height:21px;border-radius:3px;background:#e9e9e9}
</style>
</head>
<body>

<div class="abs topbar">Get Free Delivery For Every Order Above $100
  <svg class="close" width="22" height="22" viewBox="0 0 22 22" fill="none" stroke="#fff" stroke-width="1.6"><circle cx="11" cy="11" r="9.5"/><path d="M7.5 7.5l7 7M14.5 7.5l-7 7"/></svg>
</div>

<header class="abs nav">
  <div class="abs brand">Brimcraft</div>
  <nav class="abs menu"><span class="active">Home</span><span>About</span><span>Shop</span><span>Reviews</span><span>FAQs</span><span>Contact</span></nav>
  <div class="abs nav-icons">
    <span style="position:relative"><svg width="28" height="28" viewBox="0 0 24 24" fill="none" stroke="#fff" stroke-width="1.7"><path d="M12 20s-7-4.4-7-10a4 4 0 0 1 7-2.6A4 4 0 0 1 19 10c0 5.6-7 10-7 10z"/></svg><span class="badge">0</span></span>
    <svg width="28" height="28" viewBox="0 0 24 24" fill="none" stroke="#fff" stroke-width="1.7"><path d="M2 4h3l2.5 11h11L21 7H6.5"/><circle cx="9" cy="19" r="1.4"/><circle cx="17" cy="19" r="1.4"/></svg>
    <svg width="28" height="28" viewBox="0 0 24 24" fill="none" stroke="#fff" stroke-width="2"><circle cx="10.5" cy="10.5" r="6.5"/><path d="M15.5 15.5L20 20"/></svg>
  </div>
</header>

<section class="abs hero">
  <svg class="abs hero-streaks" width="1200" height="490" viewBox="0 0 1200 490" fill="none">
    <path d="M0 330L330 0M40 490L520 10M-60 260L200 0M150 490L560 80" stroke="#c1121c" stroke-opacity=".35" stroke-width="2"/>
    <path d="M0 120L370 490M90 0L600 490" stroke="#c1121c" stroke-opacity=".2" stroke-width="2"/>
  </svg>
  <div class="abs hero-photo" role="img" aria-label="Smiling man in a straw hat, sunglasses and a yellow shirt"></div>
  <h1 class="abs display"><span class="hl">High-Quality</span> Caps,<br>Fully Customized</h1>
  <p class="abs">Lorem ipsum dolor sit amet, consectetur adipiscing elit, sed do eiusmod tempor incididunt ut labore et dolore magna aliqua.</p>
  <a class="abs btn"><span class="label">Shop Now</span><span class="go"><svg width="16" height="14" viewBox="0 0 16 14" fill="none" stroke="#e0222f" stroke-width="2"><path d="M2 2l5 5-5 5M9 2l5 5-5 5"/></svg></span></a>
</section>

<section class="abs products">
  <h2 class="section-title display">Our Products
    <svg class="swoosh" width="184" height="12" viewBox="0 0 184 12"><path d="M2 9C60 2 130 1 182 5" stroke="#e0222f" stroke-width="4" fill="none" stroke-linecap="round"/></svg>
  </h2>
</section>

<div class="abs product-box">
  <div class="abs product-photo" role="img" aria-label="Straw sun hat with a tropical brim trim and a front logo patch"></div>
  <div class="dots"><span class="on"></span><span></span><span></span></div>
  <div class="abs vdivider"></div>
  <div class="abs info">
    <h2>Spotlight Hat</h2>
    <div class="stars">
      <svg width="78" height="14" viewBox="0 0 78 14" fill="#f5b400"><g id="s5"><path d="M7 0l2 4.6 5 .4-3.8 3.2 1.2 4.8L7 10.4 2.6 13l1.2-4.8L0 5l5-.4z"/></g><use href="#s5" x="16"/><use href="#s5" x="32"/><use href="#s5" x="48"/><use href="#s5" x="64"/></svg>
    </div>
    <div class="price">$20.00</div>
    <p class="desc">Lorem ipsum dolor sit amet, consectetur adipiscing elit, sed do eiusmod tempor incididunt ut labore</p>
    <div class="opt" style="top:223px">Material</div>
    <div class="select">Select <svg width="10" height="6" viewBox="0 0 10 6"><path d="M0 0h10L5 6z" fill="#fff"/></svg></div>
    <div class="opt" style="top:272px">Color</div>
    <span class="swatch" style="left:249px;background:#d9c08a"></span>
    <span class="swatch" style="left:288px;background:#d23a57"></span>
    <span class="swatch" style="left:327px;background:#0b6a4c"></span>
    <div class="opt" style="top:321px">Shape</div>
    <div class="choices" style="left:94px;top:317px"><span class="chip">Round</span><span>Square</span>|<span>Rectangle</span>|<span>Custom</span></div>
    <div class="opt" style="top:370px">Patch location</div>
    <div class="choices" style="left:150px;top:366px"><span class="chip-outline">Front</span><span>Custom</span></div>
    <div class="qty"><span>
      <svg width="14" height="2"><rect width="14" height="2" fill="#fff"/></svg></span><span>2</span><span>
      <svg width="14" height="14"><path d="M7 0v14M0 7h14" stroke="#fff" stroke-width="2"/></svg></span></div>
    <div class="actions">
      <a class="btn"><span class="label">Add To Cart</span><span class="go"><svg width="16" height="14" viewBox="0 0 16 14" fill="none" stroke="#e0222f" stroke-width="2"><path d="M2 2l5 5-5 5M9 2l5 5-5 5"/></svg></span></a>
      <a class="btn"><span class="label">Get A Quote</span><span class="go"><svg width="16" height="14" viewBox="0 0 16 14" fill="none" stroke="#e0222f" stroke-width="2"><path d="M2 2l5 5-5 5M9 2l5 5-5 5"/></svg></span></a>
    </div>
    <div class="note">Note:&nbsp; Total Cost Depending On Quantity</div>
  </div>
</div>

<div class="abs arrow-btn" style="left:109px;top:1607px"><svg width="16" height="24" viewBox="0 0 16 24" fill="none" stroke="#fff" stroke-width="3"><path d="M12 2L3 12l9 10"/></svg></div>
<div class="abs arrow-btn" style="left:1034px;top:1607px"><svg width="16" height="24" viewBox="0 0 16 24" fill="none" stroke="#fff" stroke-width="3"><path d="M4 2l9 10-9 10"/></svg></div>

<div class="thumb" style="left:155px"><div class="hat" role="img" aria-label="Straw hat with a round front patch"></div></div>
<div class="thumb" style="left:463px"><div class="hat" role="img" aria-label="Straw hat with a blue patterned brim and hexagon patch" style="background:radial-gradient(ellipse at 50% 45%,#e3d2a6 0%,#cbb27c 55%,#2e8fa8 68%,transparent 73%)"></div></div>
<div class="thumb" style="left:771px"><div class="hat" role="img" aria-label="Straw hat with a rectangular front patch"></div></div>

<div class="thumb-meta" style="left:153px"><h3>Spotlight Hat</h3><div class="stars"><svg width="64" height="12" viewBox="0 0 78 14" fill="#f5b400"><use href="#s5"/><use href="#s5" x="16"/><use href="#s5" x="32"/><use href="#s5" x="48"/><use href="#s5" x="64"/></svg></div><div class="p">$20.00</div></div>
<div class="thumb-meta" style="left:462px"><h3>Spotlight Hat</h3><div class="stars"><svg width="64" height="12" viewBox="0 0 78 14" fill="#f5b400"><use href="#s5"/><use href="#s5" x="16"/><use href="#s5" x="32"/><use href="#s5" x="48"/><use href="#s5" x="64"/></svg></div><div class="p">$20.00</div></div>
<div class="thumb-meta" style="left:770px"><h3>Spotlight Hat</h3><div class="stars"><svg width="64" height="12" viewBox="0 0 78 14" fill="#f5b400"><use href="#s5"/><use href="#s5" x="16"/><use href="#s5" x="32"/><use href="#s5" x="48"/><use href="#s5" x="64"/></svg></div><div class="p">$20.00</div></div>

<div class="abs tabs display"><span class="on">FAQs</span><span class="off">Delivery Timeline</span></div>
<div class="abs tabs-line"></div>

<div class="faq" style="top:2121px">Lorem ipsum dolor sit amet, consectetur adipiscing elit<span class="plus"><svg width="12" height="12"><path d="M6 0v12M0 6h12" stroke="#111" stroke-width="2"/></svg></span></div>
<div class="faq" style="top:2202px">Lorem ipsum dolor sit amet, consectetur adipiscing elit<span class="plus"><svg width="12" height="12"><path d="M6 0v12M0 6h12" stroke="#111" stroke-width="2"/></svg></span></div>
<div class="faq" style="top:2283px">Lorem ipsum dolor sit amet, consectetur adipiscing elit<span class="plus"><svg width="12" height="12"><path d="M6 0v12M0 6h12" stroke="#111" stroke-width="2"/></svg></span></div>
<div class="faq" style="top:2364px">Lorem ipsum dolor sit amet, consectetur adipiscing elit<span class="plus"><svg width="12" height="12"><path d="M6 0v12M0 6h12" stroke="#111" stroke-width="2"/></svg></span></div>
<div class="faq" style="top:2445px">Lorem ipsum dolor sit amet, consectetur adipiscing elit<span class="plus"><svg width="12" height="12"><path d="M6 0v12M0 6h12" stroke="#111" stroke-width="2"/></svg></span></div>
<div class="faq" style="top:2526px">Lorem ipsum dolor sit amet, consectetur adipiscing elit<span class="plus"><svg width="12" height="12"><path d="M6 0v12M0 6h12" stroke="#111" stroke-width="2"/></svg></span></div>

<h2 class="abs section-title display reviews-title">Reviews
  <svg class="swoosh" width="184" height="12" viewBox="0 0 184 12"><path d="M2 9C60 2 130 1 182 5" stroke="#e0222f" stroke-width="4" fill="none" stroke-linecap="round"/></svg>
</h2>

<article class="review" style="left:111px"><div class="q">“</div><div class="stars"><svg width="64" height="12" viewBox="0 0 78 14" fill="#f5b400"><use href="#s5"/><use href="#s5" x="16"/><use href="#s5" x="32"/><use href="#s5" x="48"/><use href="#s5" x="64"/></svg></div><p>Lorem ipsum dolor sit amet, consectetur adipiscing elit, sed do eiusmod tempor incididunt ut labore et dolore magna aliqua. Quis ipsum suspendisse ultrices gravida. Risus commodo viverra maecenas accumsan</p><div class="who"><span class="avatar">ME</span><span><b>Mara Ellison</b><small>MD at Northfield Co</small></span></div></article>
<article class="review" style="left:452px"><div class="q">“</div><div class="stars"><svg width="64" height="12" viewBox="0 0 78 14" fill="#f5b400"><use href="#s5"/><use href="#s5" x="16"/><use href="#s5" x="32"/><use href="#s5" x="48"/><use href="#s5" x="64"/></svg></div><p>Lorem ipsum dolor sit amet, consectetur adipiscing elit, sed do eiusmod tempor incididunt ut labore et dolore magna aliqua. Quis ipsum suspendisse ultrices gravida. Risus commodo viverra maecenas accumsan</p><div class="who"><span class="avatar">ME</span><span><b>Mara Ellison</b><small>MD at Northfield Co</small></span></div></article>
<article class="review" style="left:793px"><div class="q">“</div><div class="stars"><svg width="64" height="12" viewBox="0 0 78 14" fill="#f5b400"><use href="#s5"/><use href="#s5" x="16"/><use href="#s5" x="32"/><use href="#s5" x="48"/><use href="#s5" x="64"/></svg></div><p>Lorem ipsum dolor sit amet, consectetur adipiscing elit, sed do eiusmod tempor incididunt ut labore et dolore magna aliqua. Quis ipsum suspendisse ultrices gravida. Risus commodo viverra maecenas accumsan</p><div class="who"><span class="avatar">ME</span><span><b>Mara Ellison</b><small>MD at Northfield Co</small></span></div></article>

<div class="abs review-dots"><span class="on"></span><span></span><span></span><span></span></div>

<footer class="abs footer">
  <div class="col" style="left:111px"><h4>Support</h4><ul><li>Contact Us</li><li>About Us</li><li>Careers</li><li>Refund &amp; Return</li><li>Deliveries</li></ul></div>
  <div class="col" style="left:314px"><h4>Information</h4><ul><li>Search Terms</li><li>Advanced Search</li><li>Help &amp; Faq's</li><li>Store Location</li><li>Order &amp; Return</li></ul></div>
  <div class="col" style="left:527px"><h4>Help</h4><ul><li>FAQ</li><li>E-Mail Support</li><li>Live Chat</li><li>Refund &amp; Return</li><li>Store Locater</li></ul></div>
  <div class="col" style="left:729px"><h4>Subscribe To Our Newsletter</h4><p>Sed ut perspiciatis unde omnis iste natus error sit voluptatem</p>
    <div class="email">Email Address <svg width="18" height="16" viewBox="0 0 18 16"><path d="M0 7L18 0 14 16 9 10 16 3 7 9z" fill="#fff"/></svg></div></div>
</footer>
<div class="abs foot-line"></div>
<div class="abs copy">© 2025 Brimcraft. All Rights Reserved.</div>
<div class="abs cards"><span></span><span></span><span></span><span></span><span></span><span></span></div>

</body>
</html>
```